Elevating our current Business Card Design

We want to elevate our current business card with a new design to look like a zenith 300 company. We are a premium lubricant distributor (oil and grease).
We need 2 versions, version 1 is as per the uploaded a copy of our current business card with the English version.
For our Chinese version we need to use the front to be English in English and have the back of the card designed exactly like the front for all info to be in Chinese.
The design template needs to be such that we can amend the template with adding different information for each person's card.
The background colour of the card can be changed- we just need to clearly see all information on the card and logos.
The QJR and Ember steady logos cannot have any colour or display changes- only use the logos attached.
All logos need to be included and all information from the attached current card

```html
<!DOCTYPE html>
<html lang="en">
<head>
<meta charset="utf-8">
<title>KDM Business Card</title>
<link href="https://fonts.googleapis.com/css2?family=Montserrat:wght@400;500;700;800&display=swap" rel="stylesheet">
<style>
  :root {
    --stage: #1c1c1c;
    --card-front: #ffffff;
    --card-back: #c3c3c5;
    --brand-red: #e8302a;
    --cert-orange: #f05a28;
    --cert-grey: #6b6b6b;
    --eco-green: #163f2c;
    --ink: #1e1e1e;
  }
  * { margin: 0; padding: 0; box-sizing: border-box; }
  html, body { width: 1200px; height: 1059px; overflow: hidden; background: var(--stage); }
  body { position: relative; font-family: "Montserrat", sans-serif; color: var(--ink); }

  .card { position: absolute; border-radius: 20px; overflow: hidden; }
  .card--front { left: 257px; top: 86px; width: 688px; height: 400px; background: var(--card-front); }
  .card--back { left: 252px; top: 545px; width: 710px; height: 402px; background: var(--card-back); }

  .cert-badge { position: absolute; }
  .eco-badge { position: absolute; }

  .brand-name {
    position: absolute;
    font-family: "Montserrat", sans-serif;
    font-weight: 800;
    color: var(--brand-red);
    line-height: 1;
    letter-spacing: -0.02em;
  }
  .card--front .brand-name { left: 360px; top: 14px; font-size: 128px; }
  .card--back .brand-name { left: 70px; top: 20px; font-size: 250px; }

  .name-marker { position: absolute; left: 0; top: 145px; width: 18px; height: 44px; background: var(--brand-red); }
  .person { position: absolute; left: 44px; top: 142px; }
  .person__name { font-size: 25px; font-weight: 700; color: var(--brand-red); line-height: 1.1; }
  .person__role { font-size: 15px; font-weight: 500; line-height: 1.2; margin-top: 2px; }

  .contacts { position: absolute; left: 37px; top: 262px; list-style: none; }
  .contacts li { display: flex; align-items: center; height: 25.5px; font-size: 15px; font-weight: 500; }
  .contacts svg { width: 18px; height: 18px; margin-right: 16px; fill: var(--brand-red); flex: none; }

  .address { position: absolute; left: 479px; top: 292px; font-size: 16px; font-weight: 500; line-height: 1.15; }

  .partner-strip { position: absolute; left: 357px; top: 343px; }
</style>
</head>
<body>

<section class="card card--front" aria-label="Card front">
  <svg class="cert-badge" style="left:37px;top:11px" width="112" height="109" viewBox="0 0 112 109" role="img" aria-label="QJR certification badge">
    <circle cx="56" cy="54" r="50" fill="var(--cert-orange)"/>
  </svg>

  <div class="brand-name">KDM</div>

  <span class="name-marker"></span>
  <div class="person">
    <p class="person__name">Mara Vellon</p>
    <p class="person__role">Administraction Executive</p>
  </div>

  <svg class="eco-badge" style="left:532px;top:195px" width="90" height="70" viewBox="0 0 90 70" role="img" aria-label="Ember steady network member badge">
    <rect x="0" y="0" width="90" height="70" rx="10" fill="var(--eco-green)"/>
  </svg>

  <ul class="contacts">
    <li><svg viewBox="0 0 24 24"><path d="M3 9c0-3 4-5 9-5s9 2 9 5v2h-5V9H8v2H3z"/><path d="M6 12h12l2 9H4z"/><circle cx="12" cy="16" r="2.5" fill="#fff"/></svg>1300 472 615</li>
    <li><svg viewBox="0 0 24 24"><rect x="6" y="1" width="12" height="22" rx="2"/><rect x="8" y="4" width="8" height="14" fill="#fff"/><circle cx="12" cy="20.5" r="1.1" fill="#fff"/></svg>+16 430 218 904</li>
    <li><svg viewBox="0 0 24 24"><rect x="6" y="2" width="12" height="6"/><rect x="2" y="9" width="20" height="10" rx="2"/><rect x="6" y="15" width="12" height="7" fill="#fff" stroke="var(--brand-red)" stroke-width="2"/></svg>+16 8 5520 3371</li>
    <li><svg viewBox="0 0 24 24"><rect x="1" y="5" width="22" height="14" rx="1"/><path d="M2 6l10 7 10-7" fill="none" stroke="#fff" stroke-width="2"/></svg>mara.vellon@kdmsupply.com</li>
    <li><svg viewBox="0 0 24 24"><circle cx="12" cy="12" r="10"/><path d="M12 2v20M2 12h20M5 6c4 2 10 2 14 0M5 18c4-2 10-2 14 0" fill="none" stroke="#fff" stroke-width="1.4"/></svg>www.kdmsupply.com</li>
  </ul>

  <p class="address">14 Harbour Freight Way<br>Linwood, WA 6120</p>

  <svg class="partner-strip" width="292" height="44" viewBox="0 0 292 44" role="img" aria-label="KDM and Norvane Lubricants partner strip">
    <path d="M6 1h152l-6 42H1z" fill="#fff" stroke="var(--brand-red)" stroke-width="1.5"/>
    <path d="M150 0h142l-8 44H144z" fill="var(--brand-red)"/>
  </svg>
</section>

<section class="card card--back" aria-label="Card back">
  <div class="brand-name">KDM</div>

  <svg class="cert-badge" style="left:34px;top:278px" width="105" height="100" viewBox="0 0 105 100" role="img" aria-label="QJR certification badge">
    <circle cx="52" cy="50" r="46" fill="var(--cert-orange)"/>
  </svg>

  <svg class="eco-badge" style="left:556px;top:292px" width="110" height="80" viewBox="0 0 110 80" role="img" aria-label="Ember steady network member badge">
    <rect x="0" y="0" width="110" height="80" rx="12" fill="var(--eco-green)"/>
  </svg>
</section>

</body>
</html>
```